Hunting club needs a new web design !

We need a new web design for our hunting club located in Poland, called "BORYNA". The club was founded in 1945. Colors that we would like to see in the project are the colors of the forest. The website should be built in such a way that all text elements can be changed to another language and can't be graphic.
"BORYNA" means - big, thick forest in which the game, small and big resides

Target Market(s)

hunters,

Industry/Entity Type

Hunting

Coding

Coded - Design and coding required

Number of Pages Required

5+ page

Font styles to use
Decorative

Colors

Designer to choose colors to be used in the design.

Requirements
Must have
• current date, calendar,
• must contain almost all materials from our current web page
• http://boryna-lasowiec.webnest.pl/
• new web address: borynalsw.pl
Nice to have
• current weather in three hunting regions that we allowed to hunt, or indicated by the visitor on the map placed on our web,
• actual phase of the moon, actual moon rising hour, actual moon set hour, actual sun rise hour, actual sun set hour, current weather in region (stalowa wola, poland)
• wood, forest, deers, boars,
Should not have
• mountain photos, modern look, white or bright backgrounds,

```html
<!DOCTYPE html>
<html lang="en">
<head>
<meta charset="utf-8">
<title>BORYNA Hunting Club</title>
<link rel="stylesheet" href="https://fonts.googleapis.com/css2?family=Mulish:wght@400;600;700;800&family=Montserrat:wght@500;600;700&display=swap">
<style>
:root{
  --forest:#2f6d1f;
  --forest-dark:#1f4d13;
  --forest-light:#4f8f2f;
  --bark:#3b2208;
  --bark-mid:#5a3812;
  --cream:#f7f4ec;
  --ink:#333333;
  --muted:#6b6b6b;
  --white:#ffffff;
  --sky:#c9d8e6;
}
*{box-sizing:border-box;margin:0;padding:0}
html,body{width:1200px;height:3285px;overflow:hidden}
body{font-family:"Mulish",sans-serif;color:var(--ink);background:var(--white);position:relative}
.abs{position:absolute}

/* header */
.topbar{position:absolute;left:0;top:0;width:1200px;height:81px;background:var(--white)}
.search{position:absolute;left:823px;top:24px;width:246px;height:34px;border:1px solid #c8c8c8;border-radius:17px;font-size:12px;color:#999;padding:9px 18px}
.search svg{position:absolute;right:12px;top:8px}
.mainnav{position:absolute;left:0;top:81px;width:1200px;height:55px;background:linear-gradient(var(--bark-mid),var(--bark));display:flex;align-items:center}
.mainnav a{position:absolute;top:19px;color:var(--white);font:700 14px "Mulish",sans-serif;text-decoration:none}
.mainnav .sep{position:absolute;top:15px;width:1px;height:24px;background:rgba(255,255,255,.35)}
.logo{position:absolute;left:516px;top:18px;width:168px;height:168px;border-radius:50%;background:var(--forest);border:5px solid var(--white);display:flex;align-items:center;justify-content:center;color:var(--white);font:800 26px "Mulish",sans-serif;letter-spacing:2px;z-index:3}

/* hero */
.hero{position:absolute;left:0;top:136px;width:1200px;height:521px;background:linear-gradient(180deg,#6f7f8c 0%,#b9a88a 35%,#c98a3c 55%,#5d6a2c 75%,#3d4a1c 100%)}
.hero h1{position:absolute;left:0;width:1200px;top:152px;text-align:center;color:var(--white);font:600 46px/1.1 "Montserrat",sans-serif;letter-spacing:1px}
.hero h1 span{display:block;font-size:38px}
.hero .cta{position:absolute;left:515px;top:258px;width:164px;height:44px;border:2px solid var(--white);color:var(--white);font:600 16px/40px "Mulish",sans-serif;text-align:center}
.dots{position:absolute;left:556px;top:490px;display:flex;gap:10px}
.dots i{width:14px;height:14px;border-radius:50%;background:var(--white);border:2px solid var(--white)}
.dots i:first-child{background:transparent}

/* welcome */
.welcome{position:absolute;left:0;top:657px;width:1200px;height:520px;background:linear-gradient(180deg,#ffffff 0%,#f3efe6 45%,#d9cdb2 80%,#a8946a 100%)}
.welcome h2{position:absolute;left:116px;top:100px;font:500 32px "Montserrat",sans-serif;color:#3a2a14}
.welcome p{position:absolute;left:116px;width:630px;font-size:13px;line-height:21px;color:#555}
.btn-bark{position:absolute;background:var(--bark);color:var(--white);font:700 14px "Mulish",sans-serif;text-align:center}
.moonbox{position:absolute;left:766px;top:727px;width:314px;height:324px;background:var(--forest);border:8px solid var(--forest-light);border-radius:26px 0 26px 0;color:var(--white)}
.moonbox h3{text-align:center;font:600 21px "Mulish",sans-serif;margin-top:26px}
.moonbox label{position:absolute;left:26px;font-size:16px}
.moonbox .sel{position:absolute;left:104px;width:175px;height:34px;border:1px solid rgba(255,255,255,.8)}
.moonbox .sel::after{content:"";position:absolute;right:12px;top:10px;width:7px;height:7px;border-right:2px solid var(--white);border-bottom:2px solid var(--white);transform:rotate(45deg)}

/* recent hunting */
.recent{position:absolute;left:0;top:1117px;width:1200px;height:541px}
.recent h2{position:absolute;left:0;width:1200px;top:98px;text-align:center;color:var(--white);font:500 28px "Montserrat",sans-serif}
.circle{position:absolute;width:294px;height:294px;border-radius:50%;border:3px solid #e8dcc2}
.circle p{position:absolute;left:50px;top:100px;width:194px;text-align:center;color:var(--white);font-size:13px;line-height:24px}
.ctitle{position:absolute;width:320px;text-align:center;color:var(--white);font:600 19px "Mulish",sans-serif}

/* calendar */
.section-title{position:absolute;left:0;width:1200px;text-align:center;font:600 27px "Montserrat",sans-serif;color:var(--forest-dark)}
.cal{position:absolute;left:116px;top:1785px;width:291px;border:1px solid #ccc;font-size:16px}
.cal .head{height:34px;background:var(--forest-dark);color:var(--white);display:flex;justify-content:space-between;align-items:center;padding:0 14px;font-weight:700}
.cal .days,.cal .row{display:grid;grid-template-columns:repeat(7,1fr)}
.cal .days span{background:var(--forest-light);color:var(--white);text-align:center;height:26px;line-height:26px;font-size:15px}
.cal .row span{height:30px;line-height:30px;text-align:center;border-right:1px solid #ddd;border-bottom:1px solid #ddd;color:#222}
.cal .row span.o{color:#999}
.cal .row span.t{background:var(--bark);color:var(--white);font-weight:700}
.event-img{position:absolute;left:447px;width:203px;height:125px}
.event h4{position:absolute;left:668px;font:600 18px "Mulish",sans-serif;color:var(--forest)}
.event p{position:absolute;left:668px;width:400px;font-size:12.5px;line-height:19px;color:#666}
.event b{position:absolute;left:668px;font:800 12.5px "Mulish",sans-serif;color:#222}

/* weather */
.weather{position:absolute;left:0;top:2150px;width:1200px;height:369px;background:linear-gradient(180deg,#8fb0cf 0%,#c4d3df 40%,#e7dcc4 75%,#d9b77e 100%)}
.wcard{position:absolute;top:112px;width:309px;height:178px;background:var(--white);border-radius:4px;box-shadow:0 2px 8px rgba(0,0,0,.2)}
.wcard h5{text-align:center;margin-top:24px;font:700 16px "Mulish",sans-serif;color:var(--forest)}
.wcard .temp{position:absolute;left:133px;top:60px;font:400 50px "Mulish",sans-serif;color:#222}
.wcard .unit{position:absolute;left:190px;top:66px;font-size:12px;color:#333}
.wcard svg{position:absolute;left:72px;top:68px}
.wcard .meta{position:absolute;left:42px;top:140px;font-size:13px;color:#333;word-spacing:2px}

/* moon info */
.info h6{position:absolute;font:400 16px "Mulish",sans-serif;color:#222}
.info strong{position:absolute;font:400 22px "Mulish",sans-serif;color:#222}

/* footer */
.footer{position:absolute;left:0;top:2902px;width:1200px;height:322px;background:linear-gradient(180deg,#2f7a1c 0%,#2a6b18 60%,#225a13 100%)}
.footer h4{position:absolute;top:76px;color:var(--white);font:400 21px "Mulish",sans-serif}
.footer ul{position:absolute;top:120px;list-style:none;color:var(--white);font-size:14px;line-height:29px}
.contact li{display:flex;align-items:center;gap:8px}
.social{position:absolute;left:858px;top:105px;display:flex;gap:9px}
.social span{width:34px;height:34px;border-radius:50%;border:2px solid var(--white)}
.bottombar{position:absolute;left:0;top:3224px;width:1200px;height:61px;background:var(--bark);color:#c9b89a;font-size:12px;text-align:center;line-height:61px}
</style>
</head>
<body>

<header>
  <div class="topbar">
    <div class="search">Search here
      <svg width="16" height="16" viewBox="0 0 16 16"><circle cx="6.5" cy="6.5" r="5" fill="none" stroke="#888" stroke-width="1.6"/><line x1="10.3" y1="10.3" x2="14.5" y2="14.5" stroke="#888" stroke-width="1.6"/></svg>
    </div>
  </div>
  <nav class="mainnav">
    <a style="left:130px">Historia Kola</a><i class="sep" style="left:232px"></i>
    <a style="left:244px">Zarzad Kola</a><i class="sep" style="left:332px"></i>
    <a style="left:342px">Urzadzenia Lowieckie</a>
    <a style="left:690px">Etyka Lowiecka</a><i class="sep" style="left:805px"></i>
    <a style="left:817px">Plan Polowan</a><i class="sep" style="left:917px"></i>
    <a style="left:929px">Kynologia</a><i class="sep" style="left:1005px"></i>
    <a style="left:1017px">Nowosci</a>
  </nav>
  <div class="logo">BORYNA</div>
</header>

<section class="hero" role="img" aria-label="Hunter with a shotgun walking through a meadow at sunset">
  <h1>WE ARE A HUNTING CLUB<span>LOCATED IN POLAND</span></h1>
  <div class="cta">CLICK HERE</div>
  <div class="dots"><i></i><i></i><i></i><i></i></div>
</section>

<section class="welcome" role="img" aria-label="Faded photo of a hunter aiming a rifle against the evening sun">
  <h2>WELCOME TO BORYNA</h2>
  <p style="top:152px">Praesent sit amet est in dictum dolor eu dictum porttitor enim felis viverra mi eget luctus massa purus quis odio etiam nulla massa pharetra facilisis volutpat in imperdiet sit amet sem aliquam nec erat ut purus cursus interdum vestibulum ligula</p>
  <p style="top:229px">augue bibendum accumsan vestibulum ut commodo nunc morbi ornare gravida elit integer congue augue et malesuada iaculis ipsum dui aliquet felis sit et cursus magna nisl nec elit donec iaculis diam a nisi accumsan viverra duis sed tellus et tortor vestibulum</p>
  <div class="btn-bark" style="left:112px;top:344px;width:157px;height:37px;line-height:37px">READ MORE</div>
</section>

<aside class="moonbox">
  <h3>FAZY KSIEZYCA</h3>
  <label style="top:82px">Rok:</label><div class="sel" style="top:75px"></div>
  <label style="top:132px">Miesiac:</label><div class="sel" style="top:125px"></div>
  <label style="top:182px">Dzien:</label><div class="sel" style="top:175px"></div>
  <div class="btn-bark" style="left:26px;top:237px;width:254px;height:44px;line-height:44px;font-size:15px;font-weight:600">POKAZ FAZY KSIEZYCA</div>
</aside>

<section class="recent">
  <svg class="abs" style="left:0;top:0" width="1200" height="541" viewBox="0 0 1200 541" aria-hidden="true">
    <polygon points="0,133 90,56 170,80 305,10 460,30 600,0 740,28 900,14 1040,62 1110,40 1200,80 1200,541 0,541" fill="#3d8a1f"/>
    <polygon points="0,140 90,66 170,92 305,22 460,40 600,12 740,40 900,26 1040,72 1110,54 1200,92 1200,541 0,541" fill="#4a3211"/>
  </svg>
  <div class="abs" style="left:0;top:60px;width:1200px;height:481px;background:linear-gradient(180deg,rgba(59,34,8,0) 0%,rgba(40,26,8,.55) 100%)" role="img" aria-label="Dark forest background"></div>
  <h2>RECENT HUNTING</h2>
  <div class="circle" style="left:144px;top:159px;background:linear-gradient(160deg,#4c3a24,#1e1710)" role="img" aria-label="Hunter holding a rifle in a dark forest">
    <p>Aonsectetuer mi a ultricies massa est sed nisl class aptent taciti so ciosqu ad litora torquent per conubia nostra per inceptos hymenaeos</p>
  </div>
  <div class="circle" style="left:460px;top:159px;background:linear-gradient(180deg,#2b3a6e 0%,#c2506a 45%,#e08a3a 60%,#1c2230 100%)" role="img" aria-label="Hunter aiming over a lake at dusk"></div>
  <div class="circle" style="left:777px;top:159px;background:linear-gradient(160deg,#7fa060,#3d5a25 55%,#5a3315 100%)" role="img" aria-label="Hunter holding a shotgun among green reeds"></div>
  <div class="ctitle" style="left:131px;top:467px">Hunting Tittle here</div>
  <div class="ctitle" style="left:447px;top:469px">Hunting Tittle here</div>
  <div class="ctitle" style="left:764px;top:464px">Hunting Tittle here</div>
</section>

<section class="calendar-section">
  <h2 class="section-title" style="top:1712px">OUR CALENDAR</h2>
  <div class="cal">
    <div class="head"><span>&#9664;</span><span>AUG 2017</span><span>&#9654;</span></div>
    <div class="days"><span>Su</span><span>Mo</span><span>Tu</span><span>We</span><span>Th</span><span>Fr</span><span>Sa</span></div>
    <div class="row"><span class="o">28</span><span class="o">29</span><span class="o">30</span><span class="o">31</span><span>1</span><span>2</span><span>3</span></div>
    <div class="row"><span>4</span><span>5</span><span>6</span><span>7</span><span>8</span><span>9</span><span>10</span></div>
    <div class="row"><span>11</span><span>12</span><span>13</span><span>14</span><span>15</span><span>16</span><span>17</span></div>
    <div class="row"><span class="t">18</span><span>19</span><span>20</span><span>21</span><span>22</span><span>23</span><span>24</span></div>
    <div class="row"><span>25</span><span>26</span><span>27</span><span>28</span><span>29</span><span>30</span><span class="o">1</span></div>
    <div class="row"><span class="o">2</span><span class="o">3</span><span class="o">4</span><span class="o">5</span><span class="o">6</span><span class="o">7</span><span class="o">8</span></div>
  </div>
  <article class="event">
    <div class="event-img" style="top:1785px;background:linear-gradient(180deg,#b8b4a6,#7a6a4a 60%,#4a4030)" role="img" aria-label="Hunters standing in a wintry field"></div>
    <h4 style="top:1784px">Pnterdum vel blandit sed nulla In</h4>
    <p style="top:1811px">Allamcorper est eget tempor cursus neque mi consectetuer mi a ultricies massa est sed nisl class aptent taciti sociosqu ad litora torquent per conubia nostra per inceptos hymenaeos</p>
    <b style="top:1877px">READ MORE</b>
  </article>
  <article class="event">
    <div class="event-img" style="top:1934px;background:linear-gradient(180deg,#8aa6c8,#c9b46a 55%,#4a5a2a)" role="img" aria-label="Autumn forest clearing"></div>
    <h4 style="top:1934px">Suspendisse risus nibh</h4>
    <p style="top:1961px">Allamcorper est eget tempor cursus neque mi consectetuer mi a ultricies massa est sed nisl class aptent taciti sociosqu ad litora torquent per conubia nostra per inceptos hymenaeos</p>
    <b style="top:2033px">READ MORE</b>
  </article>
</section>

<section class="weather" role="img" aria-label="Misty sky over a field at sunrise">
  <h2 class="section-title" style="top:55px;color:#333;font-weight:500">CURRENT WEATHER</h2>
  <div class="wcard" style="left:118px">
    <h5>LUCTUS DICTUM</h5>
    <svg width="52" height="36" viewBox="0 0 52 36"><circle cx="18" cy="14" r="10" fill="#f2b632"/><path d="M14 32a8 8 0 0 1 2-15 11 11 0 0 1 21 2 7 7 0 0 1 3 13z" fill="#cfd6dc"/></svg>
    <div class="temp">36</div><div class="unit">°C | °F</div>
    <div class="meta">Humidity: 54% &nbsp;&nbsp;&nbsp; Wind: 11Km/h</div>
  </div>
  <div class="wcard" style="left:440px">
    <h5>LUCTUS DICTUM</h5>
    <svg width="52" height="36" viewBox="0 0 52 36"><circle cx="18" cy="14" r="10" fill="#f2b632"/><path d="M14 32a8 8 0 0 1 2-15 11 11 0 0 1 21 2 7 7 0 0 1 3 13z" fill="#cfd6dc"/></svg>
    <div class="temp">36</div><div class="unit">°C | °F</div>
    <div class="meta">Humidity: 54% &nbsp;&nbsp;&nbsp; Wind: 11Km/h</div>
  </div>
  <div class="wcard" style="left:762px">
    <h5>LUCTUS DICTUM</h5>
    <svg width="52" height="36" viewBox="0 0 52 36"><circle cx="18" cy="14" r="10" fill="#f2b632"/><path d="M14 32a8 8 0 0 1 2-15 11 11 0 0 1 21 2 7 7 0 0 1 3 13z" fill="#cfd6dc"/></svg>
    <div class="temp">36</div><div class="unit">°C | °F</div>
    <div class="meta">Humidity: 54% &nbsp;&nbsp;&nbsp; Wind: 11Km/h</div>
  </div>
</section>

<section class="info">
  <h2 class="section-title" style="top:2572px;font-size:21px;font-weight:500;color:var(--forest)">STALOWA WOLA, POLAND</h2>
  <h6 style="left:193px;top:2647px">Actual phase of the moon</h6><strong style="left:193px;top:2670px">10.00 PM</strong>
  <h6 style="left:528px;top:2645px">Actual sun rise hour</h6><strong style="left:528px;top:2668px">06.00 AM</strong>
  <h6 style="left:841px;top:2645px">Actual moon rising hour</h6><strong style="left:841px;top:2668px">09.00 PM</strong>
  <h6 style="left:193px;top:2722px">Current weather in region</h6><strong style="left:193px;top:2749px">35<small style="font-size:12px;vertical-align:top">°C|°F</small></strong>
  <h6 style="left:528px;top:2720px">Actual sun set hour</h6><strong style="left:528px;top:2743px">07.30 AM</strong>
  <h6 style="left:841px;top:2720px">Actual moon set hour</h6><strong style="left:841px;top:2743px">05.15 AM</strong>
</section>

<footer class="footer">
  <h4 style="left:138px">Contact Us</h4>
  <ul class="contact" style="left:138px">
    <li><svg width="14" height="18" viewBox="0 0 14 18"><path d="M7 0a7 7 0 0 1 7 7c0 5-7 11-7 11S0 12 0 7a7 7 0 0 1 7-7z" fill="#fff"/><circle cx="7" cy="7" r="2.6" fill="#2a6b18"/></svg>218 Oak Ridge Lane #7A</li>
    <li style="padding-left:22px">Vermont 05401 VT</li>
    <li><svg width="16" height="16" viewBox="0 0 16 16"><path d="M3 1l3 3-2 2c1 2 3 4 6 6l2-2 3 3-2 2C7 15 1 9 1 3z" fill="none" stroke="#fff" stroke-width="1.4"/></svg>512.404.7781</li>
    <li><svg width="16" height="12" viewBox="0 0 16 12"><rect x="0.7" y="0.7" width="14.6" height="10.6" fill="none" stroke="#fff" stroke-width="1.4"/><path d="M1 1l7 6 7-6" fill="none" stroke="#fff" stroke-width="1.4"/></svg>info@borynalsw.pl</li>
  </ul>
  <h4 style="left:416px">Quick Links</h4>
  <ul style="left:420px"><li>About</li><li>Gallery</li><li>Weather Update</li><li>Our Calender</li></ul>
  <h4 style="left:611px">Resources</h4>
  <ul style="left:615px"><li>Anceptos hymenaeos</li><li>Proin nulla arcu</li><li>nonummy luctus</li><li>Dictum eget</li></ul>
  <h4 style="left:861px">Follow Us</h4>
  <div class="social" aria-label="Social links"><span></span><span></span><span></span><span></span><span></span></div>
</footer>
<div class="bottombar">© 2017 Company Name &nbsp;All right reserved &nbsp;Term of Use</div>

</body>
</html>
```